Business Card Design for Training Business

Clear Path Coaching is a new business that delivers training and other services with a focus on topics related to mental health and wellbeing, for example, Wellmind Response Course, Resilience etc. We have a strong focus on evidence-based psychology and neuroscience. I have a logo which I will upload with the brief, so please consider colours that work well with the logo.
Target Market(s)
Adults, workplaces (particularly government and not-for-profits)
Industry/Entity Type
Business
Contact Information for Business Card
Head Strong TrainingSamantha SellwoodDirector0438 770 850sam@headstrongtraining.com.auwww.headstrongtraining.com.au

```html
<!DOCTYPE html>
<html lang="en">
<head>
<meta charset="utf-8">
<title>Clear Path Coaching – Business Card</title>
<link rel="stylesheet" href="https://fonts.googleapis.com/css2?family=Open+Sans:wght@300;400;700&display=swap">
<style>
  :root {
    --page: #e9e6e1;
    --card: #0b0b0c;
    --card-edge: #1c1c1e;
    --teal: #3fc4c9;
    --white: #f4f4f4;
    --grey: #9a9a9a;
    --rule: #8c8c8c;
  }
  * { margin: 0; padding: 0; box-sizing: border-box; }
  html, body {
    width: 1200px;
    height: 1022px;
    overflow: hidden;
    background: var(--page);
    font-family: "Open Sans", Arial, sans-serif;
  }
  .canvas {
    width: 1200px;
    height: 1022px;
    display: flex;
    align-items: center;
    justify-content: center;
  }
  .card {
    position: relative;
    width: 900px;
    height: 550px;
    background: linear-gradient(135deg, #1a1a1c 0%, var(--card) 45%, var(--card) 100%);
    border-radius: 22px;
    border: 1px solid var(--card-edge);
    box-shadow: 0 18px 40px rgba(0, 0, 0, 0.25);
    overflow: hidden;
  }
  .brand {
    position: absolute;
    left: 70px;
    top: 218px;
    display: flex;
    align-items: center;
    gap: 26px;
  }
  .brand-dot {
    width: 96px;
    height: 96px;
    border-radius: 50%;
    border: 2px solid var(--teal);
  }
  .brand-name {
    font-weight: 300;
    font-size: 30px;
    line-height: 1.2;
    letter-spacing: 3px;
    text-transform: uppercase;
    color: var(--grey);
  }
  .divider {
    position: absolute;
    left: 430px;
    right: 0;
    top: 286px;
    height: 1.5px;
    background: var(--rule);
  }
  .person-name {
    position: absolute;
    right: 34px;
    top: 236px;
    font-weight: 700;
    font-size: 34px;
    color: var(--white);
  }
  .person-role {
    position: absolute;
    right: 34px;
    top: 292px;
    font-weight: 400;
    font-size: 22px;
    color: var(--teal);
  }
  .contacts {
    position: absolute;
    left: 440px;
    top: 340px;
    list-style: none;
  }
  .contacts li {
    display: flex;
    align-items: center;
    gap: 14px;
    font-size: 22px;
    font-weight: 400;
    color: var(--white);
    line-height: 38px;
  }
  .contacts svg { width: 18px; height: 18px; flex: none; }
  .edge-mark {
    position: absolute;
    left: 440px;
    bottom: 0;
    width: 70px;
  }
  .edge-mark .bar-light { height: 12px; background: var(--white); }
  .edge-mark .bar-teal { height: 26px; background: var(--teal); }
</style>
</head>
<body>
<div class="canvas">
  <div class="card">
    <div class="brand">
      <div class="brand-dot"></div>
      <div class="brand-name">Clear Path<br>Coaching</div>
    </div>

    <div class="person-name">Rebecca Tanfield</div>
    <div class="divider"></div>
    <div class="person-role">Director</div>

    <ul class="contacts">
      <li>
        <svg viewBox="0 0 24 24" aria-hidden="true"><path fill="#3fc4c9" d="M6.6 10.8a15.1 15.1 0 0 0 6.6 6.6l2.2-2.2c.3-.3.7-.4 1-.2 1.1.4 2.3.6 3.6.6.6 0 1 .4 1 1V20c0 .6-.4 1-1 1A17 17 0 0 1 3 4c0-.6.4-1 1-1h3.5c.6 0 1 .4 1 1 0 1.3.2 2.5.6 3.6.1.3 0 .7-.2 1z"/></svg>
        0491 362 517
      </li>
      <li>
        <svg viewBox="0 0 24 24" aria-hidden="true"><rect x="2" y="5" width="20" height="14" rx="1.5" fill="none" stroke="#3fc4c9" stroke-width="2.2"/><path d="M3 6l9 7 9-7" fill="none" stroke="#3fc4c9" stroke-width="2.2"/></svg>
        bec@clearpathcoaching.example.au
      </li>
      <li>
        <svg viewBox="0 0 24 24" aria-hidden="true"><circle cx="12" cy="12" r="10" fill="#3fc4c9"/><path d="M2 12h20M12 2c3 3 3 17 0 20M12 2c-3 3-3 17 0 20" fill="none" stroke="#0b0b0c" stroke-width="1.4"/></svg>
        www.clearpathcoaching.example.au
      </li>
    </ul>

    <div class="edge-mark">
      <div class="bar-light"></div>
      <div class="bar-teal"></div>
    </div>
  </div>
</div>
</body>
</html>
```